Venture Capital firm needs modern business cards

We are a Venture Capital firm within financial services/Asset management. The industry generally has basic business cards with black, blue and maybe green/yellow design elements.
Our firm has a four-colour swoosh logo. We are based in London and want to stand out, just a little bit!, from the crowd. Our company is called LORV Investments and the 'C' stands for collaboration thus using makerswarm is a natural portal for our business card design competition. Our logo came via makerswarm too!
We use 'Venture Partner in Asset Management' as our tagline and this is Trademark registered. We operate in a conservative industry and we should not overstep our mark. The logo is colorful as it is and therefore the rest of the design should not be too fanciful.
The objective is twofold: make our logo element stick and memorable with our audience, whilst representing a conservative yet young image.
Updates
The Business Card obviously needs a field for Name, Surname, Job Title, Adress fields: Street, City, Postcode, Country, telefone and cell number, website address, etc.
We have uploaded the ai file. We trust that these are OK. If not, please advise.
Reason: We have have been busy with a client engagement. We will set the project as Guaranteed in return for the troubles we cause. Apologies for the confusion.
Thank you all for these great and creative design suggestions. The team is very happy with a number of your ideas! We will be in touch tomorrow to give individual feedback before the project closes on Friday. We look forward to working with some of you to narrow down your creations. Thank you, LORV Investments team.
All,
Target Market(s)
Financial Services Professionals, Investors, Media, 35-70 years, mainly male, well educated
Industry/Entity Type
Conservative
Requirements
Must have
- We must make use of our logo and potential tagline 'Venture Partner in Asset Management' as we are establishing a new Brand and new company in the market.
We can use 'LORV', 'LORV Investments', and 'LORV Investments'+tagline 'Venture Partner in Asset Management' or simply the four-colour swoosh plus the name of the company as part of the text. (see files)
All design elements are available in black or grey-scale if required. (grey scale swoosh attached).
Due to regulation we must have the following wording on the card in small print 'LORV Investments is an Appointed Representative of Bramwell Holdings Partnership Limited, which is authorised by the Monetary Oversight Board'.
Nice to have
- We would consider designs that make use of different printing techniques such embossing/debossing, UV spot etc.
We attach our colour palette in the files section for your reference.
Should not have
- The font we use for our company name is 'EXO' so do not use a font style that clashes with the corporate fonts, please.
Do not use other design elements than the ones we provide in the file library as part of this project.

```html
<!DOCTYPE html>
<html lang="en">
<head>
<meta charset="utf-8">
<title>LORV Investments – Business Card</title>
<link href="https://fonts.googleapis.com/css2?family=Exo:wght@500;700&family=Roboto:wght@300;400&display=swap" rel="stylesheet">
<style>
  :root {
    --backdrop: #ececec;
    --card: #fbfbfa;
    --card-edge: #dcdcdc;
    --ink-grey: #55585b;
    --ink-soft: #6f7275;
    --accent-green: #7cc242;
    --mark-dot: #e2336b;
  }
  * { box-sizing: border-box; margin: 0; padding: 0; }
  html, body {
    width: 1200px;
    height: 800px;
    overflow: hidden;
    background: var(--backdrop);
  }
  .sheet {
    width: 1200px;
    height: 800px;
    display: flex;
    align-items: center;
    justify-content: center;
    gap: 40px;
  }
  .card {
    position: relative;
    width: 540px;
    height: 309px;
    background: var(--card);
    border: 1px solid var(--card-edge);
    box-shadow: 0 2px 6px rgba(0,0,0,0.08);
  }

  /* Front face */
  .card--front {
    display: flex;
    align-items: center;
    justify-content: center;
  }
  .brand {
    display: flex;
    align-items: center;
    gap: 14px;
  }
  .brand__dot {
    width: 58px;
    height: 58px;
    border-radius: 50%;
    background: var(--mark-dot);
  }
  .brand__text { display: flex; flex-direction: column; }
  .brand__name {
    font-family: "Exo", sans-serif;
    font-weight: 500;
    font-size: 64px;
    line-height: 1;
    color: var(--ink-grey);
    letter-spacing: 1px;
  }
  .brand__tagline {
    font-family: "Roboto", sans-serif;
    font-weight: 400;
    font-size: 9px;
    color: var(--ink-grey);
    margin-top: 4px;
    padding-left: 3px;
  }

  /* Back face */
  .card--back {
    display: flex;
    flex-direction: column;
    align-items: center;
    padding-top: 22px;
    font-family: "Roboto", sans-serif;
    color: var(--ink-soft);
    text-align: center;
  }
  .brand--small { gap: 8px; }
  .brand--small .brand__dot { width: 28px; height: 28px; }
  .brand--small .brand__name { font-size: 34px; }
  .person__name {
    font-family: "Exo", sans-serif;
    font-weight: 700;
    font-size: 19px;
    color: var(--accent-green);
    text-transform: uppercase;
    letter-spacing: -0.3px;
    margin-top: 4px;
    line-height: 1;
  }
  .person__role {
    font-weight: 300;
    font-size: 11px;
    color: var(--ink-grey);
    margin-top: 1px;
  }
  .contact { display: flex; flex-direction: column; align-items: center; margin-top: 8px; }
  .contact__item { display: flex; flex-direction: column; align-items: center; margin-bottom: 6px; }
  .contact__icon { width: 12px; height: 12px; margin-bottom: 3px; }
  .contact__text { font-weight: 300; font-size: 10.5px; line-height: 1.25; }
  .regulatory {
    position: absolute;
    bottom: 8px;
    left: 0;
    right: 0;
    font-weight: 300;
    font-size: 6px;
    color: var(--ink-soft);
    text-align: center;
  }
</style>
</head>
<body>
<main class="sheet">

  <section class="card card--front" aria-label="Card front">
    <div class="brand">
      <span class="brand__dot"></span>
      <div class="brand__text">
        <span class="brand__name">LORV</span>
        <span class="brand__tagline">Venture Partner in Asset Management</span>
      </div>
    </div>
  </section>

  <section class="card card--back" aria-label="Card back">
    <div class="brand brand--small">
      <span class="brand__dot"></span>
      <span class="brand__name">LORV</span>
    </div>
    <h1 class="person__name">Marcus Ellwood</h1>
    <p class="person__role">Graphic designer</p>

    <div class="contact">
      <div class="contact__item">
        <svg class="contact__icon" viewBox="0 0 12 12" aria-hidden="true">
          <rect x="3" y="0.5" width="6" height="11" rx="1" fill="none" stroke="#6f7275" stroke-width="1"/>
          <line x1="5" y1="9.6" x2="7" y2="9.6" stroke="#6f7275" stroke-width="0.8"/>
        </svg>
        <span class="contact__text">+44 20 7946 0182</span>
      </div>
      <div class="contact__item">
        <svg class="contact__icon" viewBox="0 0 12 12" aria-hidden="true">
          <rect x="0.5" y="2.5" width="11" height="7" fill="none" stroke="#6f7275" stroke-width="1"/>
          <polyline points="0.5,2.5 6,7 11.5,2.5" fill="none" stroke="#6f7275" stroke-width="1"/>
        </svg>
        <span class="contact__text">http://www.lorv.net</span>
      </div>
      <div class="contact__item">
        <svg class="contact__icon" viewBox="0 0 12 12" aria-hidden="true">
          <path d="M6 11.5 C3 7.5 2 6 2 4.2 A4 4 0 0 1 10 4.2 C10 6 9 7.5 6 11.5 Z" fill="#8a8d90"/>
          <circle cx="6" cy="4.2" r="1.5" fill="#fbfbfa"/>
        </svg>
        <address class="contact__text" style="font-style:normal">
          48 Calloway st.<br>
          Harrow Bridge Valley<br>
          London city<br>
          2200
        </address>
      </div>
    </div>

    <p class="regulatory">LORV Investments is an Appointed Representative of Bramwell Holdings Partnership Limited, which is authorised by the Monetary Oversight Board</p>
  </section>

</main>
</body>
</html>
```